Exciting adult social quiz app needs awesome modern design

A new and exciting app for couples/sexual partners is in the making. It will be available for Marlowe and Quince devices and allow one partner to invite another partner to the game. The partners will answer questions about their sexual desires and needs and then try to guess what the other one answered.

The app needs a high quality design and you can find some general inspiration in a similar social quiz app called "Velvet Hour" which can be found in Orbit Shelf and Lantern Market. I like some of the basic layouts of this app.

The design should be classy and have a theme that matches the app subject. This is a sexual get-to-know-each-other-app and not a "porn app". I imagine colors might be black and red (not a requirement) and perhaps have some structures, pictures or backgrounds showing a bit of skin. It's important that the game can be accessed by players in the public space (e.g. in a bus, car etc.) without surroundings thinking it's a sex/porn game - but also important that it's exciting in a kind of sexual way. So try to find a fine line.

As the app is for both genders, the design should accommodate this.

Please see app mockups in the attached PDF.

Initially, please show design proposals for screens 13, 16 and 23.
Please notice that screen 16 doesn't have to be exactly those 2 bars - please make some alternative score comparison graphic in your proposal.

Looking forward to seeing your proposal soon!

Target Market(s)

Couples between 18 and 50

Industry/Entity Type

Adult

Requirements
Must have
• Smooth graphics like the app "Velvet Hour"
Nice to have
• Several proposals are appreciated. Perhaps you can show your proposals with different colors and object placements so that I can see some different options.

```html
<!DOCTYPE html>
<html lang="en">
<head>
<meta charset="utf-8">
<title>Velvet Hour – Round screens</title>
<link rel="stylesheet" href="https://fonts.googleapis.com/css2?family=Inter:ital,wght@0,400;0,500;0,600;1,600&display=swap">
<style>
  :root {
    --brand-red: #fb2347;
    --bar-orange: #ff6a3a;
    --screen-grey: #e6e6e2;
    --ink: #1c1c1c;
    --muted: #8a8a8a;
    --white: #ffffff;
    --line: #d6d6d6;
    --dim: rgba(60, 60, 60, 0.55);
    --photo-dark: #2a2420;
    --photo-warm: #7a5a48;
    --skin: #c99a80;
    --ad-music-a: #3a6a4a;
    --ad-music-b: #8a3a6a;
    --ad-music-c: #3a5a9a;
    --ad-music-d: #c06a3a;
    --ad-games-a: #3aa0d8;
    --ad-games-b: #f2e8c8;
    --ad-games-c: #f0c040;
    --ad-games-d: #e0357a;
  }
  * { box-sizing: border-box; margin: 0; padding: 0; }
  html, body { width: 1200px; height: 724px; overflow: hidden; background: var(--white); }
  body { font-family: "Inter", "Helvetica Neue", Arial, sans-serif; color: var(--ink); }

  .stage { position: absolute; left: 0; top: 0; width: 1380px; height: 832px; transform: scale(0.8696); transform-origin: 0 0; }

  .screen { position: absolute; top: 132px; width: 320px; height: 568px; background: var(--screen-grey); overflow: hidden; box-shadow: 0 0 0 1px #d0d0d0; }
  .screen--round { left: 10px; }
  .screen--collect { left: 344px; }
  .screen--chat { left: 676px; }
  .screen--sent { left: 1030px; width: 322px; }

  .status-bar { position: absolute; left: 0; top: 0; width: 100%; height: 20px; background: var(--brand-red); color: var(--ink); font-size: 11.5px; display: flex; align-items: center; padding: 0 6px; }
  .status-bar .signal { letter-spacing: -1px; font-size: 9px; margin-right: 4px; }
  .status-bar .clock { position: absolute; left: 0; right: 0; text-align: center; }
  .status-bar .power { margin-left: auto; display: flex; align-items: center; gap: 4px; }
  .status-bar svg { display: block; }

  .nav-bar { position: absolute; top: 20px; left: 0; width: 100%; height: 44px; background: var(--brand-red); display: flex; align-items: center; justify-content: center; font-size: 16.5px; font-weight: 600; }

  .avatar { position: absolute; border-radius: 50%; border: 2px solid var(--white); box-shadow: 0 0 0 1px #bdbdbd; background: radial-gradient(circle at 50% 40%, var(--skin) 0 38%, var(--photo-warm) 60%, var(--photo-dark) 100%); }

  .round-intro { position: absolute; top: 84px; width: 100%; text-align: center; font-size: 16.5px; line-height: 22px; color: #333; }
  .player-label { position: absolute; left: 124px; font-size: 13.5px; }
  .score-track { position: absolute; left: 100px; width: 200px; height: 44px; background: var(--white); border: 1px solid #cfcfcf; border-radius: 22px; overflow: hidden; }
  .score-fill { height: 100%; background: linear-gradient(180deg, var(--bar-orange), var(--brand-red)); display: flex; align-items: center; justify-content: flex-end; padding-right: 8px; }
  .score-fill .winner-tag { color: #ff9a7a; font-style: italic; font-weight: 600; font-size: 19px; letter-spacing: 0.5px; }

  .button-primary { position: absolute; background: var(--brand-red); border-radius: 9px; display: flex; align-items: center; justify-content: center; font-size: 16.5px; font-weight: 500; }

  .ad-banner { position: absolute; left: 2px; top: 520px; width: 316px; height: 48px; }
  .ad-banner--music { background: linear-gradient(90deg, var(--ad-music-a) 0%, var(--ad-music-b) 30%, var(--ad-music-c) 55%, var(--ad-music-d) 85%); }
  .ad-banner--games { left: 0; top: 518px; width: 100%; height: 50px; background: linear-gradient(90deg, var(--ad-games-a) 0%, var(--ad-games-b) 25%, var(--ad-games-b) 60%, var(--ad-games-c) 80%, var(--ad-games-d) 100%); }

  .is-blurred { position: absolute; inset: 0; filter: blur(3px); }
  .dim-layer { position: absolute; inset: 64px 0 0 0; background: var(--dim); }

  .favor-sheet { position: absolute; left: 25px; top: 153px; width: 270px; height: 262px; background: rgba(255,255,255,.96); border-radius: 14px; overflow: hidden; display: flex; flex-direction: column; text-align: center; }
  .favor-sheet .sheet-title { height: 36px; line-height: 36px; color: var(--brand-red); font-size: 17px; font-weight: 500; border-bottom: 1px solid var(--line); }
  .favor-option { display: flex; align-items: center; justify-content: center; font-size: 15.5px; line-height: 20px; border-bottom: 1px solid var(--line); padding: 0 10px; }
  .favor-sheet .sheet-action { flex: 1; background: var(--brand-red); display: flex; align-items: center; justify-content: center; font-size: 16.5px; font-weight: 600; }

  .partner-card { position: absolute; top: 64px; left: 0; width: 100%; height: 96px; background: var(--white); }
  .partner-photo { position: absolute; left: 0; top: 0; width: 164px; height: 96px; border-radius: 0 100px 100px 0 / 0 140px 140px 0; background: radial-gradient(circle at 42% 45%, var(--skin) 0 22%, var(--photo-warm) 42%, var(--photo-dark) 75%); }
  .partner-name { position: absolute; left: 178px; width: 120px; top: 12px; text-align: center; font-size: 23px; }
  .nudge-button { position: absolute; left: 179px; top: 51px; width: 121px; height: 32px; background: var(--brand-red); border-radius: 9px; display: flex; align-items: center; justify-content: center; gap: 18px; font-size: 16px; font-weight: 500; }
  .nudge-button svg { margin-left: -18px; }

  .chat-heading { position: absolute; top: 180px; width: 100%; text-align: center; font-size: 16.5px; font-weight: 400; }
  .chat-bubble { position: absolute; height: 36px; background: var(--white); border: 1px solid #cfcfcf; border-radius: 18px; display: flex; align-items: center; justify-content: center; font-size: 16px; }
  .chat-time { position: absolute; font-size: 8.5px; color: var(--muted); }
  .message-field { position: absolute; left: 24px; top: 466px; width: 272px; height: 32px; background: var(--white); border: 1px solid #cfcfcf; border-radius: 16px; display: flex; align-items: center; justify-content: space-between; padding: 0 14px; font-size: 14px; }
  .message-field .placeholder { color: #a8a8a8; }
  .message-field .send { color: var(--brand-red); font-weight: 500; }

  .sent-photo { position: absolute; top: 64px; left: 0; width: 100%; height: 454px; background: radial-gradient(ellipse at 55% 38%, var(--skin) 0 14%, var(--photo-warm) 30%, #3a302a 60%, #1a1614 100%); }
  .sent-caption { position: absolute; top: 460px; width: 100%; text-align: center; color: var(--white); font-size: 16.5px; }
</style>
</head>
<body>
<div class="stage">

  <section class="screen screen--round">
    <div class="status-bar">
      <span class="signal">●●●●●</span> Carrier
      <svg width="14" height="10" viewBox="0 0 14 10" style="margin-left:5px"><path d="M1 4a9 9 0 0 1 12 0M3.5 6.3a5.5 5.5 0 0 1 7 0" fill="none" stroke="#1c1c1c" stroke-width="1.4"/><circle cx="7" cy="8.6" r="1.2" fill="#1c1c1c"/></svg>
      <span class="clock">12:34 PM</span>
      <span class="power">100% <svg width="24" height="11" viewBox="0 0 24 11"><rect x=".5" y=".5" width="21" height="10" rx="2" fill="none" stroke="#1c1c1c"/><rect x="2" y="2" width="18" height="7" rx="1" fill="#1c1c1c"/><rect x="22.3" y="3.5" width="1.5" height="4" fill="#1c1c1c"/></svg></span>
    </div>
    <header class="nav-bar">Round 1</header>
    <p class="round-intro">Winner of the Round<br>selects a sexual favor</p>

    <div class="score-track" style="top:200px"><div class="score-fill" style="width:134px"><span class="winner-tag">WINNER</span></div></div>
    <span class="player-label" style="top:179px">Milo: 73%</span>
    <div class="avatar" role="img" aria-label="Portrait photo of Milo" style="left:18px;top:156px;width:96px;height:96px"></div>

    <div class="score-track" style="top:330px"><div class="score-fill" style="width:83px"></div></div>
    <span class="player-label" style="top:309px">Sienna: 40%</span>
    <div class="avatar" role="img" aria-label="Portrait photo of Sienna" style="left:18px;top:286px;width:96px;height:96px"></div>

    <div class="button-primary" style="left:96px;top:427px;width:128px;height:40px">Continue</div>

    <aside class="ad-banner ad-banner--music" role="img" aria-label="Advert banner area"></aside>
  </section>

  <section class="screen screen--collect">
    <div class="status-bar">
      <span class="signal">●●●●●</span> Carrier
      <svg width="14" height="10" viewBox="0 0 14 10" style="margin-left:5px"><path d="M1 4a9 9 0 0 1 12 0M3.5 6.3a5.5 5.5 0 0 1 7 0" fill="none" stroke="#1c1c1c" stroke-width="1.4"/><circle cx="7" cy="8.6" r="1.2" fill="#1c1c1c"/></svg>
      <span class="clock">12:34 PM</span>
      <span class="power">100% <svg width="24" height="11" viewBox="0 0 24 11"><rect x=".5" y=".5" width="21" height="10" rx="2" fill="none" stroke="#1c1c1c"/><rect x="2" y="2" width="18" height="7" rx="1" fill="#1c1c1c"/><rect x="22.3" y="3.5" width="1.5" height="4" fill="#1c1c1c"/></svg></span>
    </div>
    <header class="nav-bar">Round 1</header>
    <div class="is-blurred" style="top:64px">
      <p class="round-intro" style="top:20px">Winner of the Round<br>selects a sexual favor</p>
      <div class="avatar" style="left:18px;top:92px;width:96px;height:96px"></div>
      <div class="score-track" style="top:136px"><div class="score-fill" style="width:134px"></div></div>
      <div class="avatar" style="left:18px;top:222px;width:96px;height:96px"></div>
      <div class="score-track" style="top:266px"><div class="score-fill" style="width:83px"></div></div>
      <div class="button-primary" style="left:96px;top:363px;width:128px;height:40px">Continue</div>
    </div>
    <div class="dim-layer"></div>

    <div class="favor-sheet">
      <div class="sheet-title">Time to collect!</div>
      <div class="favor-option" style="height:33px">Oral tonight</div>
      <div class="favor-option" style="height:51px">Be naked when I get<br>home tomorrow</div>
      <div class="favor-option" style="height:33px">Naked back massage with oil</div>
      <div class="favor-option" style="height:32px">Naked foot massage</div>
      <div class="favor-option" style="height:33px">Relic Runner outfit</div>
      <div class="sheet-action">Continue</div>
    </div>

    <aside class="ad-banner ad-banner--music" role="img" aria-label="Advert banner area"></aside>
  </section>

  <section class="screen screen--chat">
    <div class="status-bar">
      <span class="signal">●●●●●</span> Carrier
      <svg width="14" height="10" viewBox="0 0 14 10" style="margin-left:5px"><path d="M1 4a9 9 0 0 1 12 0M3.5 6.3a5.5 5.5 0 0 1 7 0" fill="none" stroke="#1c1c1c" stroke-width="1.4"/><circle cx="7" cy="8.6" r="1.2" fill="#1c1c1c"/></svg>
      <span class="clock">12:34 PM</span>
      <span class="power">100% <svg width="24" height="11" viewBox="0 0 24 11"><rect x=".5" y=".5" width="21" height="10" rx="2" fill="none" stroke="#1c1c1c"/><rect x="2" y="2" width="18" height="7" rx="1" fill="#1c1c1c"/><rect x="22.3" y="3.5" width="1.5" height="4" fill="#1c1c1c"/></svg></span>
    </div>
    <header class="nav-bar">Waiting for your turn</header>

    <div class="partner-card">
      <div class="partner-photo" role="img" aria-label="Portrait photo of partner Sienna"></div>
      <div class="partner-name">Sienna</div>
      <div class="nudge-button">
        <svg width="16" height="18" viewBox="0 0 16 18"><path d="M8 1.5c-3 0-5 2.3-5 5.3v4L1 13.5h14l-2-2.7v-4c0-3-2-5.3-5-5.3z" fill="none" stroke="#fff" stroke-width="1.6" stroke-linejoin="round"/><path d="M6 15a2 2 0 0 0 4 0" fill="none" stroke="#fff" stroke-width="1.6"/></svg>
        <span>Nudge</span>
      </div>
    </div>

    <h2 class="chat-heading">Chat</h2>

    <div class="avatar" role="img" aria-label="Sienna avatar" style="left:20px;top:212px;width:44px;height:44px"></div>
    <div class="chat-bubble" style="left:70px;top:220px;width:160px">We can chat here!</div>
    <span class="chat-time" style="left:76px;top:258px">15:42 - 19/08/14</span>

    <div class="chat-bubble" style="left:186px;top:290px;width:56px">Cool!</div>
    <div class="avatar" role="img" aria-label="Milo avatar" style="left:256px;top:281px;width:44px;height:44px"></div>
    <span class="chat-time" style="left:176px;top:330px">15:46 - 19/08/14</span>

    <div class="message-field"><span class="placeholder">Message...</span><span class="send">Send</span></div>

    <aside class="ad-banner ad-banner--games" role="img" aria-label="Advert banner area"></aside>
  </section>

  <section class="screen screen--sent">
    <div class="status-bar">
      <span class="signal">●●●●●</span> Carrier
      <svg width="14" height="10" viewBox="0 0 14 10" style="margin-left:5px"><path d="M1 4a9 9 0 0 1 12 0M3.5 6.3a5.5 5.5 0 0 1 7 0" fill="none" stroke="#1c1c1c" stroke-width="1.4"/><circle cx="7" cy="8.6" r="1.2" fill="#1c1c1c"/></svg>
      <span class="clock">12:34 PM</span>
      <span class="power">100% <svg width="24" height="11" viewBox="0 0 24 11"><rect x=".5" y=".5" width="21" height="10" rx="2" fill="none" stroke="#1c1c1c"/><rect x="2" y="2" width="18" height="7" rx="1" fill="#1c1c1c"/><rect x="22.3" y="3.5" width="1.5" height="4" fill="#1c1c1c"/></svg></span>
    </div>
    <header class="nav-bar">Your turn has been sent</header>
    <div class="sent-photo" role="img" aria-label="Full-screen portrait photo of partner Sienna"></div>
    <p class="sent-caption">Wait for Sienna to answer...</p>
    <aside class="ad-banner ad-banner--games" role="img" aria-label="Advert banner area"></aside>
  </section>

</div>
</body>
</html>
```